RW Framewell Inc Business cards

We need business cards using our existing logo but slightly modified. Right now the logo says RW Loadbearing Masonry. We want to keep the RW part of the design, but replace the Structural Concrete portion with "FRAMEWELL". Please see the attached file.
Ideally this would be a blank template so we can add Different Names, titles, and phone numbers later.
On the one side we want only the logo and on the other side the detail. I'm attaching an example for you to see.
Please reach out with any other questions. Our address and other details will be given out once we find a design we like.

Target Market(s)

Construction Industry

```html
<!DOCTYPE html>
<html lang="en">
<head>
<meta charset="utf-8">
<title>RW Framewell Inc – Business Cards</title>
<link href="https://fonts.googleapis.com/css2?family=Arimo:wght@400;700&family=Exo+2:wght@500&display=swap" rel="stylesheet">
<style>
  :root {
    --backdrop: #7a5236;
    --card-dark: #1a1b1d;
    --card-blue: #1177c0;
    --brand-blue: #1a7cc6;
    --brand-grey: #8e8e90;
    --text-light: #c3c4c6;
    --rule-grey: #505154;
    --logo-cyan: #3fdcf6;
  }
  * { margin: 0; padding: 0; box-sizing: border-box; }
  html, body {
    width: 1125px;
    height: 1200px;
    overflow: hidden;
    background: var(--backdrop);
    font-family: "Arimo", Arial, sans-serif;
  }
  .canvas { position: relative; width: 1125px; height: 1200px; }

  .card {
    position: absolute;
    left: 150px;
    width: 825px;
    height: 471px;
    overflow: hidden;
  }
  .card--front { top: 98px; background: var(--card-dark); }
  .card--back  { top: 631px; background: var(--card-blue); }

  .brand-name {
    position: absolute;
    white-space: nowrap;
    font-family: "Arimo", Arial, sans-serif;
    font-weight: 700;
    letter-spacing: 1px;
  }
  .card--front .brand-name {
    left: 126px;
    top: 188px;
    font-size: 34px;
    color: var(--brand-blue);
  }
  .card--back .brand-name {
    left: 0;
    right: 0;
    top: 205px;
    text-align: center;
    font-size: 46px;
    color: var(--logo-cyan);
  }

  .divider {
    position: absolute;
    left: 433px;
    top: 150px;
    width: 1px;
    height: 170px;
    background: var(--rule-grey);
  }

  .person { position: absolute; left: 468px; top: 150px; }
  .person__name {
    font-family: "Exo 2", Arial, sans-serif;
    font-weight: 500;
    font-size: 27px;
    letter-spacing: 0.5px;
    color: var(--brand-blue);
  }
  .person__title {
    margin-top: 2px;
    font-weight: 700;
    font-size: 18px;
    color: var(--brand-grey);
  }

  .contact-list { position: absolute; left: 472px; top: 228px; list-style: none; }
  .contact-list li {
    display: flex;
    align-items: center;
    height: 24px;
    font-size: 18px;
    color: var(--text-light);
  }
  .contact-list svg { width: 14px; height: 14px; margin-right: 10px; fill: var(--brand-blue); flex: none; }

  .base-stripe { position: absolute; left: 0; bottom: 0; width: 825px; height: 10px; }
</style>
</head>
<body>
<div class="canvas">

  <section class="card card--front">
    <div class="brand-name">RW Framewell</div>
    <div class="divider"></div>

    <div class="person">
      <div class="person__name">DANIEL HARROW</div>
      <div class="person__title">President</div>
    </div>

    <ul class="contact-list">
      <li>
        <svg viewBox="0 0 16 16"><path d="M3.5 1l2.5 3-1.5 2c.8 1.9 2.6 3.7 4.5 4.5l2-1.5 3 2.5-1.5 2.5C7.5 14 2 8.5 1 2.5z"/></svg>
        555-214-7730
      </li>
      <li>
        <svg viewBox="0 0 16 16"><path d="M4 0h8a1 1 0 0 1 1 1v14a1 1 0 0 1-1 1H4a1 1 0 0 1-1-1V1a1 1 0 0 1 1-1zm1 2v10h6V2zm3 11a1 1 0 1 0 0 2 1 1 0 0 0 0-2z"/></svg>
        555-618-2094
      </li>
      <li>
        <svg viewBox="0 0 16 16"><path d="M1 4h14v1L8 9.5 1 5zm0 2.5l7 4.5 7-4.5V13H1z"/></svg>
        info@rwframewell.com
      </li>
      <li>
        <svg viewBox="0 0 16 16"><circle cx="8" cy="8" r="7"/></svg>
        www.rwframewell.com
      </li>
    </ul>

    <svg class="base-stripe" viewBox="0 0 825 10" preserveAspectRatio="none">
      <polygon points="0,0 541,0 537,10 0,10" fill="#1a7cc6"/>
      <polygon points="545,0 825,0 825,10 541,10" fill="#8e8e90"/>
    </svg>
  </section>

  <section class="card card--back">
    <div class="brand-name">RW Framewell</div>
  </section>

</div>
</body>
</html>
```